Product Designer Business Card

Small product design, engineering and prototyping firm in need of a clean, professional business card design. To support our 3D design and drawing services, we offer 3D printing, molding, and casting of plastics, silicones, resins, etc. Our logo can still be modified/changed if necessary. The red/orange color is preferred, but may be substituted with blue or green, potentially. Either way, the colour of the logo should be match/compliment colors used throughout the design. One thought is to have the logo/contact info on one side, with the other side describing services offered, like with a small icon of 3D printer, molding, casting, and computer with a 3D model on-screen.
Industry/Entity Type
Mechanical Engineering
Contact Information for Business Card
Company: Kelvar Design
Phone: 613-582-9047
Email: mark@kelvardesign.ca

```html
<!DOCTYPE html>
<html lang="en">
<head>
<meta charset="utf-8">
<title>Kelvar Design – Business Card</title>
<link rel="stylesheet" href="https://fonts.googleapis.com/css2?family=Exo+2:wght@500;700&family=Open+Sans:wght@400;600&display=swap">
<style>
  :root {
    --bg: #d6d6d6;
    --card-dark: #0b0b0b;
    --card-dark-edge: #2a2a2a;
    --card-light: #fafafa;
    --brand-red: #d8231b;
    --ink: #2b2b2b;
    --ink-soft: #5c5c5c;
    --rule: #bdbdbd;
    --icon-light: #8a8a8a;
    --icon-dark: #2e2e2e;
    --white: #ffffff;
  }
  * { margin: 0; padding: 0; box-sizing: border-box; }
  html, body { width: 1200px; height: 900px; overflow: hidden; }
  body {
    background: radial-gradient(circle at 40% 40%, #e6e6e6, var(--bg));
    font-family: "Open Sans", sans-serif;
    position: relative;
  }
  .card {
    position: absolute;
    width: 560px;
    height: 320px;
    border-radius: 26px;
    box-shadow: 0 14px 30px rgba(0,0,0,.25);
    overflow: hidden;
  }

  /* Back: services */
  .card-back {
    left: 70px; top: 110px;
    background: linear-gradient(160deg, var(--card-dark-edge), var(--card-dark) 55%);
    color: var(--white);
  }
  .back-brand {
    position: absolute; left: 0; right: 0; top: 62px;
    display: flex; justify-content: center; align-items: center; gap: 16px;
  }
  .brand-dot { width: 46px; height: 46px; border-radius: 50%; background: currentColor; }
  .brand-name {
    font-family: "Exo 2", sans-serif; font-weight: 700;
    font-size: 50px; letter-spacing: 6px; line-height: 1;
  }
  .services {
    position: absolute; left: 0; right: 0; bottom: 48px;
    display: flex; justify-content: center; gap: 34px; list-style: none;
  }
  .service { display: flex; flex-direction: column; align-items: center; gap: 10px; width: 80px; }
  .service-icon {
    width: 62px; height: 62px;
    border: 2px solid var(--white);
    background: radial-gradient(circle at 50% 45%, var(--icon-light), var(--icon-dark) 75%);
  }
  .service-label { font-size: 14px; font-weight: 600; letter-spacing: .3px; white-space: nowrap; }

  /* Front: contact */
  .card-front {
    left: 570px; top: 470px;
    background: var(--card-light);
    color: var(--ink);
  }
  .front-brand {
    position: absolute; right: 40px; top: 42px;
    display: flex; align-items: center; gap: 14px;
    color: var(--brand-red);
  }
  .front-brand .brand-dot { width: 40px; height: 40px; }
  .front-brand .brand-name { font-size: 38px; letter-spacing: 3px; }
  .divider {
    position: absolute; left: 190px; right: 40px; top: 150px;
    border-top: 1px solid var(--rule);
  }
  .website {
    position: absolute; right: 40px; top: 164px;
    font-size: 15px; color: var(--ink);
  }
  .website em { font-style: normal; color: var(--brand-red); }
  .contact { position: absolute; left: 60px; top: 196px; }
  .person-name {
    font-family: "Exo 2", sans-serif; font-weight: 700;
    font-size: 26px; color: var(--brand-red); line-height: 1.1;
  }
  .person-title { font-size: 15px; color: var(--ink-soft); margin-bottom: 10px; }
  .contact-line { display: flex; align-items: center; gap: 10px; font-size: 15px; line-height: 1.6; }
  .contact-line svg { width: 18px; height: 18px; flex: none; }
</style>
</head>
<body>

<section class="card card-back" aria-label="Card back: services">
  <div class="back-brand">
    <span class="brand-dot" aria-hidden="true"></span>
    <span class="brand-name">Kelvar</span>
  </div>
  <ul class="services">
    <li class="service">
      <div class="service-icon" role="img" aria-label="Icon of a 3D printer"></div>
      <span class="service-label">3D Printer</span>
    </li>
    <li class="service">
      <div class="service-icon" role="img" aria-label="Icon of a molding press"></div>
      <span class="service-label">Molding</span>
    </li>
    <li class="service">
      <div class="service-icon" role="img" aria-label="Icon of a casting pour"></div>
      <span class="service-label">Casting</span>
    </li>
    <li class="service">
      <div class="service-icon" role="img" aria-label="Icon of a computer showing a 3D model"></div>
      <span class="service-label">3d Model</span>
    </li>
  </ul>
</section>

<section class="card card-front" aria-label="Card front: contact">
  <div class="front-brand">
    <span class="brand-dot" aria-hidden="true"></span>
    <span class="brand-name">Kelvar Design</span>
  </div>
  <div class="divider"></div>
  <p class="website">www.<em>kelvardesign</em>.ca</p>
  <div class="contact">
    <p class="person-name">Daniel Mercer</p>
    <p class="person-title">Managing Director</p>
    <p class="contact-line">
      <svg viewBox="0 0 18 18" aria-hidden="true"><rect x="1" y="1" width="16" height="16" rx="3" fill="none" stroke="#d8231b" stroke-width="1.6"/><path d="M6 4.5c-1 .6-1.4 1.6-.8 3.2.9 2.3 2.6 4.2 4.8 5.3 1.4.6 2.4.2 3-.8l-1.8-1.6-1.2.8c-1-.5-2-1.5-2.6-2.6l.8-1.2z" fill="#d8231b"/></svg>
      613-582-9047
    </p>
    <p class="contact-line">
      <svg viewBox="0 0 18 18" aria-hidden="true"><rect x="1" y="3.5" width="16" height="11" fill="#d8231b"/><path d="M1 3.5l8 6 8-6" fill="none" stroke="#fff" stroke-width="1.4"/></svg>
      mark@kelvardesign.ca
    </p>
  </div>
</section>

</body>
</html>
```